Mireton Dental New Mover Mailers

I have been working with a local designer to produce a mailer for a dentist. I don't think the current look or info is very good. I need a brochure that will go in the mail to a new resident moving into the service area of the dentist. In other words, an information piece that has a call to action such as an offer for cleaning or a free consultation or 2nd opinion. I will provide the current design which I don't like, along with other samples I have received in the mail myself. I am looking for an 8.5 x 11" which will fold to 8.5 x 5.5 for mailing. Fold needs to be on the bottom when looking at the mailing panel. No bleeds if possible. This mailer is meant to be effective and get action (phone call or web visit), I'm not looking for the best-looking design to win awards. We need the recipient to act with a phone call or visit to the web site. If this project meets with the client approval, there will be 3 more offices we will need to produce for.

Target Market(s)

Mailer to New Residents moving into the service area of the dentist

Industry/Entity Type

Dental

Requirements
Must have
• Call to action, picture of staff and or dentist, client logo, web-site address, phone, art which is dentist related, Accept Most Insurance Plans, Map, mailing panel, 8.5 x 11" which will fold in half to 8.5 x 5.5" for mailing, Reason why you would visit this dentist, Free Consultations, and 2nd Opinions, Welcoming New Patients, Individualized care, Sedation dentistry, Convenient dental services including Quick Align Plan, in-office Whitening, and dental implants.
Nice to have
• Picture of staff or doctor taken off web site

```html
<!DOCTYPE html>
<html lang="en">
<head>
<meta charset="utf-8">
<title>Mireton Dental – New Mover Mailer</title>
<link rel="stylesheet" href="https://fonts.googleapis.com/css2?family=Oswald:wght@500;700&family=Lato:wght@400;700&display=swap">
<style>
  :root {
    --blue: #2b44a6;
    --ink: #2a2a2a;
    --bar: #333333;
    --paper: #ffffff;
    --page: #f2f2f2;
    --panel-grey: #e6e6e6;
    --stamp: #c9c9c9;
    --photo-a: #f1e3d4;
    --photo-b: #c9a98b;
    --map-b: #d5dbe3;
  }
  * { box-sizing: border-box; margin: 0; padding: 0; }
  html, body { width: 1200px; height: 1200px; overflow: hidden; background: var(--page); }
  .sheet {
    position: absolute; left: 160px; top: 30px; width: 881px; height: 1140px;
    background: var(--paper); box-shadow: 0 4px 18px rgba(0,0,0,.18);
  }
  .panel { position: absolute; left: 0; width: 881px; height: 570px; overflow: hidden; background: var(--paper); }
  .panel--front { top: 0; transform: rotate(180deg); }
  .panel--mailing { top: 570px; border-top: 1px solid #ddd; }
  .panel svg.art { position: absolute; inset: 0; }
  .display { font-family: "Oswald", sans-serif; text-transform: uppercase; white-space: nowrap; }
  .body { font-family: "Lato", sans-serif; }

  .brand { position: absolute; display: flex; align-items: center; gap: 8px; white-space: nowrap;
    font-family: "Oswald", sans-serif; font-weight: 700; color: var(--blue); text-transform: uppercase; letter-spacing: .5px; }
  .brand__mark { width: 14px; height: 14px; background: var(--blue); }

  /* front */
  .front__brand { left: 470px; top: 34px; font-size: 26px; }
  .front__offer-a { position: absolute; left: 470px; top: 78px; font-size: 60px; font-weight: 700; color: var(--blue); line-height: 1; }
  .front__offer-b { position: absolute; left: 470px; top: 148px; font-size: 60px; font-weight: 700; color: var(--ink); line-height: 1; letter-spacing: -1px; }
  .front__phone-bar { position: absolute; left: 452px; top: 230px; width: 429px; height: 72px; background: var(--bar); }
  .front__phone { position: absolute; left: 470px; top: 230px; font-size: 60px; font-weight: 700; color: #fff; line-height: 72px; letter-spacing: -1px; }
  .front__social { position: absolute; left: 470px; top: 335px; display: flex; align-items: center; gap: 12px; color: var(--blue); font-family: "Lato", sans-serif; }
  .front__social-dot { width: 52px; height: 52px; background: var(--blue); border-radius: 6px; }
  .front__social-text { font-size: 30px; line-height: 1.05; }
  .front__social-text strong { display: block; font-weight: 400; color: var(--ink); font-size: 42px; }
  .front__cta { position: absolute; left: 345px; top: 500px; color: #fff; font-size: 18px; line-height: 1.2; white-space: nowrap; }
  .front__url { position: absolute; left: 620px; top: 510px; color: #fff; font-family: "Oswald", sans-serif; font-size: 24px; font-weight: 500; white-space: nowrap; }

  /* mailing */
  .mail__brand { left: 66px; top: 24px; font-size: 24px; }
  .mail__heading { position: absolute; left: 26px; font-family: "Oswald", sans-serif; font-weight: 500; color: var(--blue); font-size: 24px; white-space: nowrap; }
  .mail__list { position: absolute; list-style: none; font-family: "Lato", sans-serif; font-size: 14px; color: var(--ink); line-height: 1.25; }
  .mail__list li { position: relative; padding-left: 12px; margin-bottom: 4px; }
  .mail__list li::before { content: ""; position: absolute; left: 0; top: 6px; width: 5px; height: 5px; border-radius: 50%; background: var(--blue); }
  .mail__rule { position: absolute; left: 30px; top: 348px; width: 370px; height: 1px; background: #ddd; }
  .mail__contact { position: absolute; left: 34px; font-family: "Lato", sans-serif; font-size: 14px; color: var(--ink); line-height: 1.3; font-style: normal; }
  .mail__contact h3 { font-family: "Oswald", sans-serif; font-weight: 500; color: var(--blue); font-size: 17px; text-transform: uppercase; }
  .mail__stamp { position: absolute; left: 757px; top: 22px; width: 94px; height: 100px; background: var(--stamp); }
  .mail__address { position: absolute; left: 530px; top: 282px; width: 341px; height: 196px; background: var(--panel-grey);
    padding: 62px 20px; font-family: "Lato", sans-serif; font-size: 13px; line-height: 1.35; color: var(--ink); white-space: nowrap; }
</style>
</head>
<body>
<main class="sheet">

  <section class="panel panel--front">
    <svg class="art" width="881" height="570" viewBox="0 0 881 570">
      <defs>
        <linearGradient id="photoTone" x1="0" y1="0" x2="1" y2="1">
          <stop offset="0" stop-color="var(--photo-a)"/>
          <stop offset="1" stop-color="var(--photo-b)"/>
        </linearGradient>
      </defs>
      <path d="M0,410 C260,480 560,410 881,480 L881,570 L0,570 Z" fill="var(--blue)"/>
      <path d="M0,398 C260,468 560,398 881,468" fill="none" stroke="var(--ink)" stroke-width="10"/>
      <circle cx="205" cy="310" r="205" fill="none" stroke="var(--ink)" stroke-width="12"/>
      <circle cx="200" cy="306" r="188" fill="var(--paper)" stroke="var(--blue)" stroke-width="8"/>
      <circle cx="200" cy="306" r="176" fill="url(#photoTone)" role="img" aria-label="Photo of a smiling family of four"/>
    </svg>
    <div class="brand front__brand"><span class="brand__mark"></span>Mireton Dental</div>
    <div class="display front__offer-a">A Free</div>
    <div class="display front__offer-b">Consultation</div>
    <div class="front__phone-bar"></div>
    <div class="display front__phone">702.555.0148</div>
    <div class="front__social"><span class="front__social-dot"></span><span class="front__social-text">Find us on<strong>Friendsite</strong></span></div>
    <p class="body front__cta">We need the recipient to act<br>with visit to the website</p>
    <div class="front__url">miretondental.com</div>
  </section>

  <section class="panel panel--mailing">
    <svg class="art" width="881" height="570" viewBox="0 0 881 570">
      <path d="M420,0 C330,120 420,200 430,300 C440,400 440,480 445,570" fill="none" stroke="var(--ink)" stroke-width="12"/>
      <path d="M445,0 C360,120 445,200 455,300 C465,400 465,480 470,570" fill="none" stroke="var(--blue)" stroke-width="8"/>
      <circle cx="333" cy="442" r="82" fill="none" stroke="var(--ink)" stroke-width="5"/>
      <circle cx="333" cy="442" r="76" fill="var(--map-b)" role="img" aria-label="Street map showing the office location"/>
    </svg>
    <div class="brand mail__brand"><span class="brand__mark"></span>Mireton Dental</div>

    <h2 class="mail__heading" style="top:68px">why you would visit this dentist</h2>
    <ul class="mail__list" style="left:26px; top:116px; width:165px">
      <li>Welcoming New Patients</li>
      <li>Individualized care</li>
      <li>Sedation dentistry</li>
    </ul>
    <ul class="mail__list" style="left:200px; top:116px; width:176px">
      <li>Convenient dental services including Quick Align Plan</li>
      <li>In-office Whitening and dental implants</li>
    </ul>

    <h2 class="mail__heading" style="top:218px">why you would visit this dentist</h2>
    <ul class="mail__list" style="left:26px; top:262px; width:340px">
      <li>We will ensure you pay as little out-of-pocket as possible for all services!</li>
      <li>Affordable in-house dental coverage so you can stay current with dental needs.</li>
    </ul>

    <div class="mail__rule"></div>
    <address class="mail__contact" style="top:372px">
      <h3>Visit Our Office</h3>
      <strong>Mireton Dental</strong><br>
      2140 Harrow Ridge Ave<br>
      Northfield, NV 89000
      <h3 style="margin-top:10px">Give Us A Shout</h3>
      hello@miretondental.com<br>
      (702) 555-0148
    </address>

    <div class="mail__stamp"></div>
    <div class="mail__address">
      3/3/574/************AUTO**SCH 5-DIGIT 89000<br>
      Harlow Family<br>
      1187 Juniper Bend Ct<br>
      Northfield, NV 89000-0100
    </div>
  </section>

</main>
</body>
</html>
```